Veldmark Supplies Business Card

Professional business card that stand out to our potential customers. Front and back with clean modern design

Industry/Entity Type

Oil and gas

Contact Information for Business Card

Name, address, website , office phone and cell number

Requirements
Must have
• Editable files for each employee

```html
<!DOCTYPE html>
<html lang="en">
<head>
<meta charset="utf-8">
<title>Veldmark Supplies – Business Card</title>
<link href="https://fonts.googleapis.com/css2?family=Montserrat:wght@400;500;700;800&display=swap" rel="stylesheet">
<style>
  :root {
    --cyan: #0eafd3;
    --red: #e42228;
    --white: #ffffff;
    --ink: #161616;
    --stage: #3a3a3a;
  }
  * { box-sizing: border-box; margin: 0; padding: 0; }
  html, body { width: 1200px; height: 689px; overflow: hidden; }
  body {
    background: var(--stage);
    font-family: "Montserrat", Arial, sans-serif;
    position: relative;
  }
  .card {
    position: absolute;
    top: 190px;
    width: 540px;
    height: 309px;
    overflow: hidden;
  }
  .card-front { left: 30px; background: var(--cyan); }
  .card-back { left: 630px; background: var(--white); }

  .wordmark {
    display: flex;
    align-items: center;
    gap: 12px;
    color: var(--white);
    font-weight: 800;
    text-transform: uppercase;
    letter-spacing: 1px;
    white-space: nowrap;
  }
  .wordmark-square { display: block; background: currentColor; }
  .card-front .wordmark {
    position: absolute;
    left: 0; right: 0; top: 130px;
    justify-content: center;
    font-size: 36px;
  }
  .card-front .wordmark-square { width: 30px; height: 30px; }

  .card-back .wordmark {
    position: absolute;
    left: 26px; top: 150px;
    color: var(--red);
    font-size: 16px;
    gap: 8px;
  }
  .card-back .wordmark-square { width: 14px; height: 14px; }

  .back-art { position: absolute; inset: 0; }

  .contact {
    position: absolute;
    left: 292px; top: 24px;
    color: var(--ink);
    z-index: 1;
  }
  .contact-name {
    color: var(--red);
    font-weight: 800;
    font-size: 19px;
    letter-spacing: 0.5px;
    text-transform: uppercase;
    line-height: 1.2;
  }
  .contact-title { font-size: 12px; margin-top: 2px; }
  .contact-address { font-size: 11.5px; line-height: 1.35; margin-top: 9px; }
  .contact-list { list-style: none; margin-top: 9px; }
  .contact-list li {
    display: flex; align-items: center; gap: 8px;
    font-size: 11.5px; margin-bottom: 5px;
    white-space: nowrap;
  }
  .icon {
    width: 15px; height: 15px; flex: none;
    background: var(--red);
    display: flex; align-items: center; justify-content: center;
  }
  .icon svg { width: 11px; height: 11px; }
  .accent { color: var(--red); }
</style>
</head>
<body>

  <section class="card card-front" aria-label="Card front">
    <div class="wordmark"><span class="wordmark-square"></span>Veldmark Supplies</div>
  </section>

  <section class="card card-back" aria-label="Card back">
    <svg class="back-art" viewBox="0 0 540 309" preserveAspectRatio="none" aria-hidden="true">
      <line x1="226" y1="42" x2="262" y2="160" stroke="var(--red)" stroke-width="1"/>
      <line x1="238" y1="28" x2="276" y2="172" stroke="var(--cyan)" stroke-width="1"/>
      <line x1="252" y1="46" x2="282" y2="138" stroke="var(--red)" stroke-width="1"/>
      <path d="M0 309 L0 274 C150 270 300 256 380 228 C440 210 490 204 540 200 L540 309 Z" fill="var(--cyan)"/>
      <path d="M0 258 C160 252 290 240 362 214 C300 250 160 266 0 270 Z" fill="var(--red)"/>
    </svg>

    <div class="wordmark"><span class="wordmark-square"></span>Veldmark Supplies</div>

    <div class="contact">
      <p class="contact-name">Dara Holloway</p>
      <p class="contact-title">President</p>
      <p class="contact-address">4820 Caddo Ridge Rd, Ste<br>210, Midland, TX 79705</p>
      <ul class="contact-list">
        <li><span class="icon"><svg viewBox="0 0 12 12"><path d="M2 4 Q6 1 10 4 L9 5.5 L7.5 5 L7.5 4 Q6 3.5 4.5 4 L4.5 5 L3 5.5 Z M3 6.5 H9 V10 H3 Z" fill="#fff"/></svg></span>432-555-0148</li>
        <li><span class="icon"><svg viewBox="0 0 12 12"><rect x="3.5" y="1" width="5" height="10" rx="1" fill="none" stroke="#fff" stroke-width="1.2"/></svg></span>000-000-9999</li>
        <li><span class="icon"><svg viewBox="0 0 12 12"><rect x="1.5" y="3" width="9" height="6" fill="none" stroke="#fff" stroke-width="1"/><path d="M1.5 3 L6 6.5 L10.5 3" fill="none" stroke="#fff" stroke-width="1"/></svg></span>info@example-youremail.com</li>
        <li><span class="icon"><svg viewBox="0 0 12 12"><circle cx="6" cy="6" r="4.5" fill="none" stroke="#fff" stroke-width="1"/><path d="M1.5 6 H10.5 M6 1.5 Q3.5 6 6 10.5 M6 1.5 Q8.5 6 6 10.5" fill="none" stroke="#fff" stroke-width="0.8"/></svg></span><span>www.<span class="accent">example-yourwebsite</span>.com</span></li>
      </ul>
    </div>
  </section>

</body>
</html>
```